Custom Seed Packet design for Flower Farm

We need a design for our seeds packets.
The design will be a kind of "fill in the blanks" as we need the design to be adaptable for multiple varieties of seed. We will be using the design for a rubber stamp.
Our seed packets are 90x90mm in size.
Black logo only. No colour required.
A vintage botanical influence is desired.
Will need to include the following info,
"Wrenfield Gable Co logo" , "Seeds", "Plant Type", "Variety", "Harvested"

```html
<!DOCTYPE html>
<html lang="en">
<head>
<meta charset="utf-8">
<title>Wrenfield Gable Co – Flower Seed Packet</title>
<link href="https://fonts.googleapis.com/css2?family=Cormorant+Garamond:wght@500&family=Pinyon+Script&display=swap" rel="stylesheet">
<style>
  :root {
    --page: #ffffff;
    --kraft: #d9c7a3;
    --kraft-light: #e3d4b4;
    --ink: #2b2723;
    --ink-soft: #4a4540;
    --banner: #5a554e;
    --banner-dark: #3b3732;
    --banner-text: #e6d7b8;
  }
  * { box-sizing: border-box; margin: 0; padding: 0; }
  html, body { width: 1122px; height: 1200px; overflow: hidden; background: var(--page); }
  .canvas { position: relative; width: 1122px; height: 1200px; }

  .packet-label {
    position: absolute; left: 111px; top: 150px;
    width: 900px; height: 900px;
  }
  .ornament-border {
    position: absolute; inset: 0;
    background: radial-gradient(circle at 50% 50%, var(--ink-soft), var(--ink) 75%);
    border: 3px solid var(--ink);
  }
  .label-panel {
    position: absolute; inset: 70px;
    background: radial-gradient(circle at 50% 45%, var(--kraft-light), var(--kraft) 80%);
    border: 4px solid var(--ink);
  }

  .seeds-banner { position: absolute; left: -4px; top: 18px; width: 720px; height: 140px; }
  .banner-word {
    font-family: "Cormorant Garamond", serif; font-weight: 500;
    font-size: 64px; letter-spacing: 18px; fill: var(--banner-text);
  }
  .banner-tag { font-family: "Pinyon Script", cursive; font-size: 34px; fill: var(--banner-text); }

  .botanical-art {
    position: absolute; left: 220px; top: 175px; width: 220px; height: 190px;
    border-radius: 50% 50% 40% 40%;
    background: radial-gradient(circle at 55% 45%, rgba(43,39,35,0.28), rgba(43,39,35,0.06) 70%);
  }

  .brand-name {
    position: absolute; left: 0; right: 0; top: 395px;
    text-align: center;
    font-family: "Cormorant Garamond", serif; font-weight: 500;
    font-size: 48px; color: var(--ink);
  }

  .fill-fields { position: absolute; left: 55px; right: 60px; top: 545px; }
  .field { display: flex; align-items: flex-end; height: 60px; }
  .field-label {
    font-family: "Pinyon Script", cursive; font-size: 26px; color: var(--ink);
    white-space: nowrap; padding-right: 10px; line-height: 1;
  }
  .field-line { flex: 1; border-bottom: 2px solid var(--ink); margin-bottom: 4px; }
</style>
</head>
<body>
<div class="canvas">
  <section class="packet-label">
    <div class="ornament-border" role="img" aria-label="Ornate vintage swirl border in black on kraft"></div>
    <div class="label-panel">
      <svg class="seeds-banner" viewBox="0 0 720 140" aria-hidden="false">
        <path d="M0 100 Q60 78 150 72 L150 122 Q60 124 0 140 Z" fill="var(--banner-dark)"/>
        <path d="M130 48 Q380 10 700 36 L700 96 Q380 70 130 108 Z" fill="var(--banner)"/>
        <text class="banner-word" x="455" y="86" text-anchor="middle">SEEDS</text>
        <text class="banner-tag" x="18" y="126" transform="rotate(-8 18 126)">Flower</text>
      </svg>

      <div class="botanical-art" role="img" aria-label="Line drawing of three poppy flowers on stems"></div>

      <div class="brand-name">Wrenfield Gable Co</div>

      <div class="fill-fields">
        <div class="field"><span class="field-label">Plant Type</span><span class="field-line"></span></div>
        <div class="field"><span class="field-label">Variety</span><span class="field-line"></span></div>
        <div class="field"><span class="field-label">Harvested</span><span class="field-line"></span></div>
      </div>
    </div>
  </section>
</div>
</body>
</html>
```